I need new business cards designed

I would like to get some new designs on business cards. I will upload my logo for reference. The business cards that were designed for me a few months ago were too difficult for the print companies to work with. My company is Quillbrook.net LLC. It is an art company that sells painting and expression cards online.

```html
<!DOCTYPE html>
<html lang="en">
<head>
<meta charset="UTF-8">
<title>Quillbrook.net LLC — Business Card</title>
<link href="https://fonts.googleapis.com/css2?family=Open+Sans:wght@400;600;800&display=swap" rel="stylesheet">
<style>
  :root {
    --page-bg: #3a3a3a;
    --card-bg: #171717;
    --brand-indigo: #3d3f8f;
    --accent-blue: #13a3de;
    --accent-orange: #f7941d;
    --text-light: #f2f2f2;
  }
  * { box-sizing: border-box; margin: 0; padding: 0; }
  html, body { width: 1200px; height: 900px; overflow: hidden; }
  body {
    background: var(--page-bg);
    font-family: "Open Sans", Arial, sans-serif;
    position: relative;
  }
  .card {
    position: absolute;
    left: 250px;
    width: 700px;
    height: 400px;
    background: var(--card-bg);
    border-radius: 22px;
    overflow: hidden;
  }
  .card--front { top: 40px; }
  .card--back { top: 470px; }

  .brand { display: flex; align-items: center; }
  .brand__square { background: var(--accent-orange); flex: none; }
  .brand__name { color: var(--brand-indigo); font-weight: 600; line-height: 1; white-space: nowrap; }

  .card--front .brand { position: absolute; left: 130px; top: 150px; gap: 22px; }
  .card--front .brand__square { width: 100px; height: 100px; }
  .card--front .brand__name { font-size: 54px; }

  .card--back .brand { position: absolute; left: 60px; top: 268px; gap: 14px; }
  .card--back .brand__square { width: 56px; height: 56px; }
  .card--back .brand__name { font-size: 28px; }

  .divider {
    position: absolute; left: 372px; top: 70px;
    width: 2px; height: 260px; background: var(--accent-blue);
  }
  .contact { position: absolute; left: 398px; top: 70px; color: var(--text-light); }
  .contact__name {
    color: var(--accent-blue); font-weight: 800; font-size: 30px; letter-spacing: 0.5px; line-height: 1.1;
  }
  .contact__role { font-size: 16px; margin-top: 2px; }
  .contact__address { font-size: 16px; margin-top: 16px; line-height: 1.55; }
  .contact__list { list-style: none; margin-top: 16px; font-size: 16px; line-height: 1.6; }
  .contact__list li { display: flex; align-items: center; gap: 8px; }
  .contact__icon { width: 15px; height: 15px; fill: var(--accent-blue); flex: none; }

  .social { position: absolute; right: 38px; bottom: 82px; display: flex; gap: 10px; }
  .social__dot { width: 16px; height: 16px; border-radius: 50%; background: var(--accent-blue); }
</style>
</head>
<body>

<section class="card card--front" aria-label="Card front">
  <div class="brand">
    <span class="brand__square"></span>
    <span class="brand__name">Quillbrook.net</span>
  </div>
</section>

<section class="card card--back" aria-label="Card back">
  <div class="brand">
    <span class="brand__square"></span>
    <span class="brand__name">Quillbrook.net</span>
  </div>

  <div class="divider"></div>

  <div class="contact">
    <div class="contact__name">MAREN ELLIS</div>
    <div class="contact__role">Managing Director</div>
    <div class="contact__address">Your address, City<br>State, Zip 1234</div>
    <ul class="contact__list">
      <li>
        <svg class="contact__icon" viewBox="0 0 16 16" aria-hidden="true"><path d="M3 1h3l1.5 4-2 1.3a9 9 0 0 0 4.2 4.2L11 8.5l4 1.5v3a2 2 0 0 1-2 2A12 12 0 0 1 1 3a2 2 0 0 1 2-2z"/></svg>
        123-456-7890
      </li>
      <li>
        <svg class="contact__icon" viewBox="0 0 16 16" aria-hidden="true"><path d="M1 3h14L8 8.5z"/><path d="M1 4.8l7 5.5 7-5.5V13H1z"/></svg>
        hello@quillbrookmail.net
      </li>
      <li>
        <svg class="contact__icon" viewBox="0 0 16 16" aria-hidden="true"><circle cx="8" cy="8" r="7"/></svg>
        Www.Quillbrook.net
      </li>
    </ul>
  </div>

  <div class="social" aria-label="Social profiles">
    <span class="social__dot"></span>
    <span class="social__dot"></span>
    <span class="social__dot"></span>
  </div>
</section>

</body>
</html>
```